RW Holloway LLC Business Card - Civil Engineering & Consulting Firm

We need a Business Card that is elegant, and masculine.  It is our Professional Civil Engineering & Consulting Company located in San Antonio TX (Not s construction or builder firm- no gears & no tool images please). We provide civil engineering services including  commercial site plans, grading and drainage plans, utility plans, hydraulics and hydrology, land planning, utility coordination, and other general civil engineering services related to commercial and residential development.
We have 2 existing Logos. We would like to convey reliability, strength, trustworthiness and attention to detail.  Blues and orange tones as per logo We are OK with the use of a darker blue in the mix.  We have 2 logo versions - Full Company Name Logo to go on the back of card, & Small Icon Logo for the front w/ personal Info.

Target Market(s)
Architects, Real Estate Developers, Other Strctural Engineers, Surveyers, General Contractors
Industry/Entity Type
Professional Civil Engineering
Contact Information for Business Card
Name, Position, Address, Cell & Office #, email, and company website
Font styles to use
Other font styles liked:
- Avian
Requirements
Should not have
- No Tools, No Gears, no Cranes, or Construction Equipment.

```html
<!DOCTYPE html>
<html lang="en">
<head>
<meta charset="utf-8">
<title>RW Holloway LLC Business Card</title>
<link href="https://fonts.googleapis.com/css2?family=Montserrat:wght@400;500;700&display=swap" rel="stylesheet">
<style>
  :root {
    --backdrop: #3a3a3a;
    --card: #1c1c1c;
    --card-pattern-a: #161616;
    --card-pattern-b: #2a2a2a;
    --sky-blue: #7fb0e0;
    --orange: #f0931e;
    --white: #f2f2f2;
    --rule: #6f9fd0;
  }
  * { box-sizing: border-box; margin: 0; padding: 0; }
  html, body { width: 1200px; height: 801px; overflow: hidden; }
  body {
    background: var(--backdrop);
    font-family: "Montserrat", Arial, sans-serif;
    color: var(--white);
    position: relative;
  }
  .card {
    position: absolute;
    top: 252px;
    width: 520px;
    height: 297px;
    background: var(--card);
    border-bottom: 2px solid var(--sky-blue);
    border-left: 1px solid var(--sky-blue);
    box-shadow: 0 10px 30px rgba(0,0,0,.45);
    overflow: hidden;
  }
  .card--front { left: 60px; }
  .card--back { left: 620px; }

  /* front */
  .brand {
    position: absolute;
    right: 44px;
    top: 46px;
    display: flex;
    align-items: center;
    gap: 10px;
  }
  .brand__mark {
    width: 14px; height: 14px;
    background: var(--orange);
  }
  .brand__name {
    font-size: 24px;
    font-weight: 500;
    letter-spacing: 1px;
    color: var(--sky-blue);
  }
  .divider {
    position: absolute;
    left: 230px; right: 0;
    top: 108px;
    height: 1px;
    background: var(--rule);
  }
  .address {
    position: absolute;
    right: 36px;
    top: 140px;
    text-align: right;
    font-size: 13px;
    line-height: 1.45;
  }
  .person {
    position: absolute;
    left: 40px;
    top: 150px;
  }
  .person__name {
    font-size: 17px;
    font-weight: 700;
    color: var(--sky-blue);
    letter-spacing: .5px;
  }
  .person__role {
    font-size: 13px;
    margin-top: 2px;
  }
  .person__rule {
    width: 190px;
    height: 1px;
    background: var(--rule);
    margin: 10px 0 8px;
  }
  .contacts { list-style: none; }
  .contacts li {
    display: flex;
    align-items: center;
    gap: 8px;
    font-size: 12.5px;
    line-height: 19px;
  }
  .contacts svg { width: 11px; height: 11px; flex: none; }

  /* back */
  .monogram-field {
    position: absolute; inset: 0;
    background: repeating-linear-gradient(90deg, var(--card-pattern-a) 0 22px, var(--card-pattern-b) 22px 26px, var(--card-pattern-a) 26px 48px);
    opacity: .8;
  }
  .back-brand {
    position: absolute;
    right: 60px;
    top: 136px;
    font-size: 15px;
    font-weight: 500;
    color: var(--orange);
    background: var(--card);
    padding: 4px 8px;
  }
</style>
</head>
<body>
  <section class="card card--front">
    <div class="brand">
      <span class="brand__mark"></span>
      <span class="brand__name">RW Holloway LLC</span>
    </div>
    <div class="divider"></div>
    <p class="address">1840 Riverbend Plaza<br>San Antonio TX 78205</p>
    <div class="person">
      <p class="person__name">DANIEL REYES</p>
      <p class="person__role">President</p>
      <div class="person__rule"></div>
      <ul class="contacts">
        <li><svg viewBox="0 0 12 12"><rect x="3" y="1" width="6" height="10" rx="1" fill="none" stroke="#f0931e" stroke-width="1.4"/></svg>555-310-4827</li>
        <li><svg viewBox="0 0 12 12"><path d="M2 2c0 5 3 8 8 8l1-2-2-1-1 1c-2-1-3-2-4-4l1-1-1-2z" fill="#f0931e"/></svg>555-310-4828</li>
        <li><svg viewBox="0 0 12 12"><rect x="1" y="3" width="10" height="7" fill="#f0931e"/><path d="M1 3l5 4 5-4" fill="none" stroke="#1c1c1c" stroke-width="1"/></svg>info@rwhollowayconsulting.com</li>
        <li><svg viewBox="0 0 12 12"><circle cx="6" cy="6" r="5" fill="#f0931e"/><path d="M1 6h10M6 1v10" stroke="#1c1c1c" stroke-width="1"/></svg>www.rwhollowayconsulting.com</li>
      </ul>
    </div>
  </section>

  <section class="card card--back">
    <div class="monogram-field" role="img" aria-label="Repeating tone-on-tone company monogram pattern"></div>
    <span class="back-brand">RW Holloway LLC</span>
  </section>
</body>
</html>
```